Wordpress Web Design & Coding for velcorahealth.ca

We need a website for a new investment company that is visually grabbing and vibrant. We would like to see a web page that displays trust, growth and confidence. Needs to be responsive and mobile friendly for all browsers and coded for both Android & IOS.

Open to the number of pages and menu items. I selected 4 but if you feel the layout would work better with less I am open to this. Need to sell the people (management team/related businesses) and then show where the invested money will be going (upcoming projects).

Company Info:

Vel Cora is an investment company put together by a group of seasoned business professionals who have come together to combine decades of success in the real estate development, management, financing and medical services. The company will be a full service company offering turn key solutions for medical professionals.

Vel-Cora will focus on providing a full range of services via a group of distinct companies to deliver newly emerging needs of the medical community. The end goal will be to create complete solutions for individuals in the medical community. Our group has experience and success with the conceptualization, construction and financing of medical and dental clinic spaces. Vel-Cora Solutions will be established to accommodate all areas of the development and creation of clinics for medical professionals from building construction to equipment financing and administrations.

You can mention these companies and take photos from their websites. You can also use stock photos.

Our construction partner:
https://318bld.com/projects/

Our equipment leasing partner:
https://www.norvixa.com/

Our Management Team and medical partners

Gil Parish
https://www.ourfirmstance.ca/

Dietmar Vellasquin
https://www.gshdentalservices.com/about-us

PROPOSED PROJECTS (see attachment for details)
Pinegrove Business Park
Holtmere Business Park
Mt. Corwin Ridge Professional

Target Market(s)

Investors

Industry/Entity Type

Investment

Coding

Coded - Design and coding required

Number of Pages Required

4 page

Font styles to use
Sans Serif

Requirements
Must have
• Wordpress – must be both desktop and mobile friendly with fast page load speed
Ability to edit after ourselves in Wordpress
Attractive home page with logo etc.
Logo colours are: for the blue the pantone color is #0355a3
and for the green is #8cc63f

Sections, about us, what we do/services we provide, contact us

```html
<!DOCTYPE html>
<html lang="en">
<head>
<meta charset="utf-8">
<title>About Us – Vel-Cora Solutions</title>
<link rel="stylesheet" href="https://fonts.googleapis.com/css2?family=Mulish:wght@400;600;700;800&family=Oswald:wght@500&display=swap">
<style>
:root{
  --blue:#0355a3;
  --green:#8cc63f;
  --ink:#3a3a3a;
  --black:#000;
  --grey-bg:#f1f1f1;
  --footer:#232323;
  --white:#fff;
  --muted:#777;
}
*{box-sizing:border-box;margin:0;padding:0}
html,body{width:1200px;height:2872px;overflow:hidden}
body{font-family:'Mulish',sans-serif;color:var(--ink);background:var(--white);position:relative}
.abs{position:absolute}

.topbar{left:0;top:0;width:1200px;height:69px;background:var(--black)}
.top-contact{display:flex;align-items:center;gap:10px;color:#fff;font-size:16px;font-weight:600;letter-spacing:.3px}
.dot-icon{width:32px;height:32px;border-radius:50%;background:var(--green);display:flex;align-items:center;justify-content:center}
.nav{left:0;top:69px;width:1200px;height:64px;background:#fff;box-shadow:0 1px 3px rgba(0,0,0,.08)}
.nav a{position:absolute;top:0;height:64px;line-height:64px;font-weight:800;font-size:15px;color:#222;text-decoration:none;letter-spacing:.5px;text-align:center}
.nav a.active{background:var(--blue);color:#fff}
.logo-card{left:132px;top:0;width:244px;height:173px;background:#fff;border-radius:0 0 30px 30px;box-shadow:0 3px 8px rgba(0,0,0,.15);display:flex;flex-direction:column;align-items:center;justify-content:center;gap:8px;z-index:3}
.logo-mark{width:28px;height:28px;background:var(--blue)}
.logo-name{font-weight:800;font-size:26px;color:var(--blue);text-align:center;line-height:1.05;letter-spacing:.5px}

.hero{left:0;top:133px;width:1200px;height:400px;background:linear-gradient(100deg,#e9e4df 0%,#c9d6e6 35%,#8fb1d6 60%,#4c83c3 100%)}
.hero-title{right:128px;top:298px;font-family:'Oswald',sans-serif;font-size:52px;color:#fff;text-shadow:0 2px 6px rgba(0,0,0,.35);letter-spacing:.5px}

.section-title{font-weight:800;font-size:34px;color:var(--blue);letter-spacing:1px}
.section-title .hl{color:var(--green)}
.title-rule{width:44px;height:3px;background:#d0e3f5;margin-top:12px}

.about-img{left:132px;top:611px;width:425px;height:401px;background:linear-gradient(135deg,#1f66b8 0%,#0355a3 55%,#8cc63f 100%)}
.about-text{left:586px;top:620px;width:484px}
.about-text p{font-size:16.2px;line-height:26.4px;letter-spacing:.15px;text-align:justify;margin-top:11px}
.about-text p:first-of-type{margin-top:20px}
.about-wide{left:133px;top:1049px;width:937px;font-size:16.8px;line-height:26.4px;letter-spacing:.3px;text-align:justify}

.team{left:0;top:1221px;width:1200px;height:1227px;background:var(--grey-bg)}
.team-head{left:0;top:1307px;width:1200px;text-align:center}
.team-head .title-rule{margin:12px auto 0}
.tab{position:absolute;width:230px;height:44px;border:1px solid #d6d6d6;background:#fff;font-weight:800;font-size:14px;letter-spacing:.4px;color:#222;display:flex;align-items:center;justify-content:center;border-radius:2px}
.tab.active{background:var(--blue);color:#fff;border-color:var(--blue)}
.profile{left:132px;top:1525px;width:938px;height:820px;background:#fff;box-shadow:0 1px 6px rgba(0,0,0,.08)}
.portrait{left:139px;top:1533px;width:294px;height:376px;background:linear-gradient(160deg,#9a9a9a 0%,#6f6f6f 60%,#5a5a5a 100%)}
.bio{left:462px;top:1568px;width:577px}
.bio h3{font-weight:800;font-size:23px;color:var(--blue);letter-spacing:.8px}
.brand-line{margin-top:12px;height:30px;font-size:22px;font-weight:600;color:var(--muted);line-height:30px}
.bio p{font-size:15.5px;line-height:27.2px;letter-spacing:.2px;text-align:justify;margin-top:10px}
.bio p.first{margin-top:8px}
.sign{left:462px;top:2208px;width:170px;height:36px;background:linear-gradient(90deg,#e8e8e8,#f6f6f6)}
.sign-name{left:462px;top:2272px;font-size:17px;font-weight:600;color:#222;letter-spacing:.4px}

.footer{left:0;top:2448px;width:1200px;height:375px;background:var(--footer)}
.footer-col{color:#fff}
.f-head{font-weight:800;font-size:15px;color:var(--green);letter-spacing:.8px}
.f-rule{width:48px;height:2px;background:var(--green);margin-top:14px}
.f-divider{top:2520px;width:1px;height:240px;background:#3a3a3a}
.links li{list-style:none;font-size:14px;line-height:29px;color:#eee}
.links li::before{content:"»";margin-right:7px;color:#bbb}
.c-row{display:flex;gap:14px;margin-top:20px}
.c-icon{width:32px;height:32px;border-radius:50%;background:var(--blue);flex:none;display:flex;align-items:center;justify-content:center}
.c-row strong{display:block;font-size:14px;font-weight:700;letter-spacing:.4px;color:#fff}
.c-row span{display:block;font-size:13.5px;line-height:22px;color:#ddd}
.social{display:flex;align-items:center;gap:14px;height:32px;margin-top:15px;font-size:15px;color:#fff}
.social i{width:32px;height:32px;border-radius:50%;display:block}
.f-logo{left:859px;top:2590px;width:208px;text-align:center}
.f-logo .logo-mark{margin:0 auto 10px}
.copyright{left:0;top:2823px;width:1200px;height:49px;background:var(--blue);color:#fff;font-size:14px;text-align:center;line-height:49px}
.copyright b{font-weight:800}
</style>
</head>
<body>

<header>
  <div class="abs topbar"></div>
  <div class="abs top-contact" style="left:658px;top:17px">
    <span class="dot-icon"><svg width="16" height="16" viewBox="0 0 24 24"><path fill="#fff" d="M6.6 10.8a15 15 0 0 0 6.6 6.6l2.2-2.2c.3-.3.7-.4 1-.2 1.1.4 2.3.6 3.6.6.6 0 1 .4 1 1V20c0 .6-.4 1-1 1A17 17 0 0 1 3 4c0-.6.4-1 1-1h3.5c.6 0 1 .4 1 1 0 1.3.2 2.5.6 3.6.1.3 0 .7-.2 1z"/></svg></span>780-555-0142
  </div>
  <div class="abs top-contact" style="left:836px;top:17px">
    <span class="dot-icon"><svg width="16" height="16" viewBox="0 0 24 24"><rect x="3" y="6" width="18" height="12" rx="2" fill="none" stroke="#fff" stroke-width="2"/><path d="M3 7l9 6 9-6" fill="none" stroke="#fff" stroke-width="2"/></svg></span>info@velcorahealth.ca
  </div>
  <nav class="abs nav">
    <a href="#" style="left:535px;width:84px">HOME</a>
    <a href="#" class="active" style="left:638px;width:136px">ABOUT US</a>
    <a href="#" style="left:790px;width:134px">WHAT WE DO</a>
    <a href="#" style="left:948px;width:140px">CONTACT US</a>
  </nav>
  <div class="abs logo-card">
    <span class="logo-mark"></span>
    <span class="logo-name">VEL-CORA<br>SOLUTIONS</span>
  </div>
</header>

<section>
  <div class="abs hero" role="img" aria-label="Doctor's hand touching a digital interface of medical icons over a blurred hospital corridor"></div>
  <h1 class="abs hero-title">ABOUT US</h1>
</section>

<section>
  <div class="abs about-img" role="img" aria-label="Blue medical cross with a green tick, filled with a faint office photo"></div>
  <div class="abs about-text">
    <h2 class="section-title">ABOUT <span class="hl">US</span></h2>
    <div class="title-rule"></div>
    <p>We are a group of seasoned business professionals who have come together to combine decades of success in the real estate development, management, financing and medical services industries. This wide foundation of experience built on prior success, will be used to strengthen existing industry partnerships. As well, new relationships will be developed to augment the existing group’s strengths. The ultimate goal will be to enhance individual earnings and equity growth for our investors.</p>
    <p>As we embark on this newest chapter, our combined knowledge will build on the discussions of the privatization in medial services that are ongoing at this time.</p>
  </div>
  <p class="abs about-wide">The fundamental relationship of medical practitioners to their respective provincial governments is changing dramatically. One of our strategic goals is to assist the medical community in identifying and participating in opportunities that arise in the next 10 years.</p>
</section>

<section>
  <div class="abs team"></div>
  <div class="abs team-head">
    <h2 class="section-title">OUR MANAGEMENT <span class="hl">TEAM</span></h2>
    <div class="title-rule"></div>
  </div>
  <div class="tab active" style="left:132px;top:1390px">GIL PARISH</div>
  <div class="tab" style="left:368px;top:1390px">DIETMAR VELLASQUIN</div>
  <div class="tab" style="left:605px;top:1390px">WENDELL HASKO</div>
  <div class="tab" style="left:841px;top:1390px">MARCUS TOLLEVIN, CPA</div>
  <div class="tab" style="left:368px;top:1446px">ANDERS QUILLBY</div>
  <div class="tab" style="left:612px;top:1446px">RUPERT HALE-DUNMORE</div>

  <div class="abs profile"></div>
  <div class="abs portrait" role="img" aria-label="Portrait of Dr. Gil Parish in a white clinic coat against a grey backdrop"></div>
  <div class="abs bio">
    <h3>GIL PARISH</h3>
    <div class="brand-line">Firm Stance</div>
    <p class="first">Dr. Parish graduated with a degree in Family Medicine in 1983. He practiced medicine as a solo rural general practitioner for 6 years. He then completed a residency in Obstetrics &amp; Gynecology at the University of Northcrest.</p>
    <p>Gil joined a group practice at the Harwick Hospital, where he practiced for 24 years. In 2000 he opened Radiant Touch For You which has since become known as Firm Stance Longevity &amp; Med Spa which offers medical aesthetics and laser spa services. He continues to focus on Bio-identical hormone replacement therapy out of Firm Stance, which has grown to three locations and continues to serve the greater Kelvane area. During the expansion of Firm Stance over the last 20 years, Gil has been fortunate to becoming active as an owner-operator of commercial and real estate space. Twelve years ago, Gil purchased commercial real estate for Firm Stance Fenwick Park. This has become a part of a very successful long term retirement strategy. In 2015, Gil was able to participate in a land purchase, property development and building construction which led to the ultimate purchase of commercial space for the Firm Stance Ashford Glen location. Gil was able to purchase excess space at this site and become a commercial landlord. These activities have given Gil a deep understanding about commercial real estate opportunities for the self-employed physician.</p>
  </div>
  <div class="abs sign" role="img" aria-label="Handwritten signature"></div>
  <div class="abs sign-name">DR GIL PARISH, M.D. FRCS(C)</div>
</section>

<footer>
  <div class="abs footer"></div>
  <div class="abs footer-col" style="left:134px;top:2520px">
    <div class="f-head">QUICK LINKS</div>
    <div class="f-rule"></div>
    <ul class="links" style="margin-top:10px">
      <li>Home</li><li>About Us</li><li>What We Do</li><li>Contact Us</li>
    </ul>
  </div>
  <div class="abs f-divider" style="left:282px"></div>
  <div class="abs footer-col" style="left:328px;top:2520px;width:260px">
    <div class="f-head">CONTACT DETAILS</div>
    <div class="f-rule"></div>
    <div class="c-row" style="margin-top:18px">
      <span class="c-icon"><svg width="14" height="16" viewBox="0 0 24 24"><path fill="#fff" d="M12 2a7 7 0 0 0-7 7c0 5 7 13 7 13s7-8 7-13a7 7 0 0 0-7-7zm0 9.5A2.5 2.5 0 1 1 12 6.5a2.5 2.5 0 0 1 0 5z"/></svg></span>
      <div><strong>VEL-CORA SOLUTIONS</strong><span>#314, 7 Larchmont Road<br>Fenwick Park, AB T4K 2M9</span></div>
    </div>
    <div class="c-row">
      <span class="c-icon"><svg width="14" height="14" viewBox="0 0 24 24"><path fill="#fff" d="M6.6 10.8a15 15 0 0 0 6.6 6.6l2.2-2.2c.3-.3.7-.4 1-.2 1.1.4 2.3.6 3.6.6.6 0 1 .4 1 1V20c0 .6-.4 1-1 1A17 17 0 0 1 3 4c0-.6.4-1 1-1h3.5c.6 0 1 .4 1 1 0 1.3.2 2.5.6 3.6.1.3 0 .7-.2 1z"/></svg></span>
      <div><strong>PHONE</strong><span>780-555-0142</span></div>
    </div>
    <div class="c-row">
      <span class="c-icon"><svg width="14" height="14" viewBox="0 0 24 24"><rect x="3" y="6" width="18" height="12" rx="1" fill="#fff"/><path d="M3 7l9 6 9-6" fill="none" stroke="#0355a3" stroke-width="2"/></svg></span>
      <div><strong>EMAIL</strong><span>info@velcorahealth.ca</span></div>
    </div>
  </div>
  <div class="abs f-divider" style="left:598px"></div>
  <div class="abs footer-col" style="left:643px;top:2520px">
    <div class="f-head">FOLLOW US ON</div>
    <div class="f-rule"></div>
    <div class="social" style="margin-top:16px"><i style="background:#1c5bbd"></i>Friendbook</div>
    <div class="social"><i style="background:#14a8d9"></i>Chirper</div>
    <div class="social"><i style="background:#0f7fba"></i>Linkwork</div>
    <div class="social"><i style="background:#d9212e"></i>Snapgram</div>
  </div>
  <div class="abs f-divider" style="left:815px"></div>
  <div class="abs f-logo">
    <span class="logo-mark" style="display:block"></span>
    <span class="logo-name" style="font-size:32px">VEL-CORA<br>SOLUTIONS</span>
  </div>
  <div class="abs copyright">Copyright © 2020 <b>VEL-CORA SOLUTIONS</b>. All Rights Reserved.</div>
</footer>

</body>
</html>
```